Looking for a modern, Professional business card design

We have a simple business card, but are looking for a more modern, professional look. A sample of the basic card is attached as well as the logo. We would also like to add that we offer:
Struggling with your finances?
- Learn to become debt free
- Discover the power of cash
- Control your money instead of it controlling you
Let us help you achieve a new level of financial freedom!
Also, we would like to have a "SPECIAL OFFER!: FREE 30 minute consultation"
Financial Planning

```html
<!DOCTYPE html>
<html lang="en">
<head>
<meta charset="utf-8">
<title>Steadfast Financial Coaching – Business Card</title>
<link rel="stylesheet" href="https://fonts.googleapis.com/css2?family=Open+Sans:ital,wght@0,400;0,600;0,700;0,800;1,400&display=swap">
<style>
  :root {
    --bg: #e9e7e2;
    --card-dark: #0d0d0d;
    --card-light: #ffffff;
    --green: #6fbf2a;
    --green-deep: #4e9e1c;
    --green-light: #9bd24e;
    --text-light: #ffffff;
    --text-dark: #222222;
    --text-muted: #666666;
  }
  * { box-sizing: border-box; margin: 0; padding: 0; }
  html, body { width: 1200px; height: 843px; overflow: hidden; }
  body {
    background: var(--bg);
    font-family: "Open Sans", Arial, sans-serif;
    position: relative;
  }
  .card {
    position: absolute;
    left: 290px;
    width: 620px;
    height: 354px;
    border-radius: 22px;
    overflow: hidden;
    box-shadow: 0 8px 24px rgba(0,0,0,0.18);
  }
  /* Back side */
  .card--back { top: 48px; background: var(--card-dark); color: var(--text-light); }
  .card--back .brand { position: absolute; left: 40px; top: 34px; }
  .brand { display: flex; align-items: center; gap: 12px; }
  .brand__dot { width: 26px; height: 26px; border-radius: 50%; background: var(--green); flex: none; }
  .brand__name { font-weight: 800; font-size: 26px; line-height: 1.05; letter-spacing: 0.5px; text-transform: uppercase; }
  .card--back .brand__name { color: var(--text-light); }
  .brand__tagline { font-size: 11px; color: var(--text-muted); margin-top: 4px; }
  .card--back .brand__tagline { color: #9a9a9a; }

  .pitch { position: absolute; left: 40px; top: 142px; right: 30px; }
  .pitch__headline { color: var(--green); font-weight: 700; font-size: 18px; letter-spacing: 0.3px; }
  .pitch__list { list-style: none; margin-top: 4px; }
  .pitch__list li { font-size: 17px; line-height: 1.32; padding-left: 18px; position: relative; }
  .pitch__list li::before { content: ""; position: absolute; left: 2px; top: 9px; width: 7px; height: 7px; border-radius: 50%; background: var(--text-light); }
  .pitch__close { font-size: 17px; line-height: 1.32; }
  .offer__title { color: var(--green); font-weight: 700; font-size: 22px; margin-top: 4px; }
  .offer__detail { font-weight: 700; font-size: 16px; }

  /* Front side */
  .card--front { top: 442px; background: var(--card-light); color: var(--text-dark); }
  .card--front .brand { position: absolute; left: 210px; top: 40px; }
  .card--front .brand__name { color: var(--text-dark); }
  .card--front .brand__dot { background: var(--green); }

  .contact-band { position: absolute; left: 0; right: 0; bottom: 0; height: 230px; }
  .contact {
    position: absolute; left: 150px; top: 210px; right: 20px;
    color: var(--text-light);
    white-space: nowrap;
  }
  .contact__name { font-size: 20px; font-weight: 600; display: flex; gap: 12px; }
  .contact__title { font-weight: 400; }
  .contact__row { display: flex; align-items: center; gap: 8px; font-size: 16px; margin-top: 6px; }
  .contact__row svg { flex: none; }
  .contact__pair { display: flex; gap: 24px; }
</style>
</head>
<body>

  <section class="card card--back" aria-label="Business card, back">
    <div class="brand">
      <span class="brand__dot"></span>
      <div>
        <div class="brand__name">Steadfast Financial Coaching</div>
        <div class="brand__tagline">Achieve a new level of personal freedom</div>
      </div>
    </div>

    <div class="pitch">
      <h2 class="pitch__headline">STRUGGLING WITH YOUR FINANCES?</h2>
      <ul class="pitch__list">
        <li>Learn to become debt free</li>
        <li>Discover the power of cash</li>
        <li>Control your money instead of it controlling you</li>
      </ul>
      <p class="pitch__close">Let us help you achieve a new level of financial freedom!</p>
      <p class="offer__title">SPECIAL OFFER!</p>
      <p class="offer__detail">FREE 30 minute consultation</p>
    </div>
  </section>

  <section class="card card--front" aria-label="Business card, front">
    <div class="brand">
      <span class="brand__dot"></span>
      <div>
        <div class="brand__name">Steadfast<br>Financial Coaching</div>
        <div class="brand__tagline">Achieve a new level of personal freedom</div>
      </div>
    </div>

    <svg class="contact-band" viewBox="0 0 620 230" preserveAspectRatio="none" aria-hidden="true">
      <defs>
        <linearGradient id="bandGradient" x1="0" y1="0" x2="1" y2="1">
          <stop offset="0" stop-color="#a6d95a"/>
          <stop offset="0.5" stop-color="#6fbf2a"/>
          <stop offset="1" stop-color="#4e9e1c"/>
        </linearGradient>
      </defs>
      <path d="M0 70 L620 20 L620 230 L0 230 Z" fill="url(#bandGradient)"/>
    </svg>

    <div class="contact">
      <div class="contact__name"><span>Daniel R. Hale</span><span>–</span><span class="contact__title">Personal Financial Coach</span></div>
      <div class="contact__pair">
        <div class="contact__row">
          <svg width="14" height="20" viewBox="0 0 14 20" aria-hidden="true"><rect x="1" y="1" width="12" height="18" rx="2" fill="none" stroke="#fff" stroke-width="1.8"/><circle cx="7" cy="15.5" r="1.2" fill="#fff"/></svg>
          <span>(205) 555-0182</span>
        </div>
        <div class="contact__row">
          <svg width="20" height="14" viewBox="0 0 20 14" aria-hidden="true"><rect x="1" y="1" width="18" height="12" rx="1.5" fill="none" stroke="#fff" stroke-width="1.8"/><path d="M1.5 1.5 L10 8 L18.5 1.5" fill="none" stroke="#fff" stroke-width="1.6"/></svg>
          <span>daniel@steadyledgercoach.com</span>
        </div>
      </div>
      <div class="contact__row">
        <svg width="18" height="18" viewBox="0 0 18 18" aria-hidden="true"><circle cx="9" cy="9" r="8" fill="none" stroke="#fff" stroke-width="1.6"/><ellipse cx="9" cy="9" rx="3.5" ry="8" fill="none" stroke="#fff" stroke-width="1.3"/><path d="M1 9 H17" stroke="#fff" stroke-width="1.3"/></svg>
        <span>www.steadyledgercoach.com</span>
      </div>
    </div>
  </section>

</body>
</html>
```